Business Card for a mobile physiotherapy company

I need a layout for a business card for a mobile physiotherapy company.
Slogan is "Mobile Physiotherapy - Your Road To Recovery"
Phone number is 867-555-0142
Email VardenTherapy@postnest.ca (subject to change with website)
Website www.VardenTherapy.ca
My name and credentials: Luke Varden Luke Varden, BSc(kin), MPT, CAFCI, IMS
Information maybe included: Direct Billing, Services including Physiotherapy, IMS, acupuncture
Maybe include facebook and instagram logos
One side with the logo clean and sharp
Other side with details, try not to look too busy, keep everything concise

```html
<!DOCTYPE html>
<html lang="en">
<head>
<meta charset="utf-8">
<title>Varden Therapy – Business Card</title>
<link rel="stylesheet" href="https://fonts.googleapis.com/css2?family=Lato:wght@400;700&family=Roboto:wght@400&display=swap">
<style>
  :root {
    --page-bg: #161616;
    --card-bg: #232323;
    --ink-white: #f4f4f4;
    --ink-silver: #c9c9c9;
    --brand-blue: #2f5689;
    --icon-blue: #3d5f8f;
  }
  * { box-sizing: border-box; margin: 0; padding: 0; }
  html, body {
    width: 1200px; height: 900px; overflow: hidden;
    background: var(--page-bg);
    font-family: "Lato", Arial, sans-serif;
  }
  .sheet {
    width: 1200px; height: 900px;
    display: flex; flex-direction: column; align-items: center; justify-content: center;
    gap: 44px;
  }
  .card {
    width: 640px; height: 366px;
    background: var(--card-bg);
    position: relative;
  }
  /* Front side */
  .card--front {
    display: flex; align-items: center; justify-content: center; gap: 16px;
  }
  .wordmark {
    font-family: "Lato", Arial, sans-serif;
    font-weight: 700;
    letter-spacing: 0.14em;
    text-transform: uppercase;
  }
  .card--front .wordmark { font-size: 40px; color: var(--ink-silver); }
  .wordmark-square { width: 18px; height: 18px; background: var(--ink-silver); }
  /* Back side */
  .card--back {
    display: flex; align-items: center; padding: 0 44px;
  }
  .brand-block { width: 280px; display: flex; align-items: center; gap: 12px; }
  .card--back .wordmark { font-size: 28px; color: var(--ink-white); line-height: 1.2; }
  .brand-square { width: 14px; height: 14px; background: var(--brand-blue); flex-shrink: 0; }
  .divider { width: 2px; height: 236px; background: var(--ink-white); margin: 0 30px 0 6px; }
  .details { color: var(--ink-white); }
  .details__name {
    font-family: "Roboto", Arial, sans-serif;
    color: var(--brand-blue);
    font-size: 26px; line-height: 1.12; margin-bottom: 8px;
  }
  .details__services { font-size: 15px; line-height: 1.35; margin-bottom: 12px; }
  .contact { list-style: none; font-size: 16px; }
  .contact li { display: flex; align-items: center; gap: 12px; line-height: 1.7; }
  .contact svg { width: 12px; height: 12px; flex-shrink: 0; }
</style>
</head>
<body>
<main class="sheet">
  <section class="card card--front" aria-label="Card front">
    <span class="wordmark-square"></span>
    <span class="wordmark">Varden Therapy</span>
  </section>

  <section class="card card--back" aria-label="Card back">
    <div class="brand-block">
      <span class="brand-square"></span>
      <span class="wordmark">Varden<br>Therapy</span>
    </div>
    <div class="divider"></div>
    <div class="details">
      <h1 class="details__name">Luke Varden, BSc(kin),<br>MPT, CAFCI, IMS</h1>
      <p class="details__services">Direct Billing, Services including<br>Physiotherapy, IMS, acupuncture</p>
      <ul class="contact">
        <li>
          <svg viewBox="0 0 12 12" aria-hidden="true"><path d="M2.5 1 L4.5 1 L5 3.5 L3.8 4.3 Q4.8 6.8 7.7 8.2 L8.5 7 L11 7.5 L11 9.5 Q10.5 11 9 11 Q1 10 1 2.5 Q1 1 2.5 1 Z" fill="var(--icon-blue)"/></svg>
          867-555-0142
        </li>
        <li>
          <svg viewBox="0 0 12 12" aria-hidden="true"><rect x="1" y="2.5" width="10" height="7" fill="none" stroke="var(--icon-blue)" stroke-width="1.2"/><path d="M1 2.5 L6 6.5 L11 2.5" fill="none" stroke="var(--icon-blue)" stroke-width="1.2"/></svg>
          VardenTherapy@postnest.ca
        </li>
        <li>
          <svg viewBox="0 0 12 12" aria-hidden="true"><circle cx="6" cy="6" r="5" fill="none" stroke="var(--icon-blue)" stroke-width="1.1"/><ellipse cx="6" cy="6" rx="2.2" ry="5" fill="none" stroke="var(--icon-blue)" stroke-width="1"/><path d="M1 6 H11" stroke="var(--icon-blue)" stroke-width="1"/></svg>
          www.VardenTherapy.ca
        </li>
      </ul>
    </div>
  </section>
</main>
</body>
</html>
```